New Business Cards for Tormin Group

We need a new Business Card to compliment our new logo. We are a vibrant design, manufacture and install business providing recreation areas, public parks and Municipal spaces. We want business cards that are classy, modern and clean.

We have recently changed our logo, and are celebrating our 40th anniversary. We want business cards with a new modern design to reflect our status.

Target Market(s)

Customers

Contact Information for Business Card

We need all the details of our 3 offices as per the business card attached. Please disregard the old logo on the business card, the other three files show our new logo.

Requirements
Must have
• All info as per attached business card but with new logo.
Nice to have

```html
<!DOCTYPE html>
<html lang="en">
<head>
<meta charset="utf-8">
<title>Tormin Group – Business Card</title>
<link rel="stylesheet" href="https://fonts.googleapis.com/css2?family=Lato:wght@400;700;900&display=swap">
<style>
  :root {
    --bg: #5e5e5e;
    --card: #ffffff;
    --red: #ec2f39;
    --ink: #3a3a3a;
    --text: #333333;
    --charcoal: #3d3f44;
  }
  * { box-sizing: border-box; margin: 0; padding: 0; }
  html, body { width: 1200px; height: 1200px; overflow: hidden; }
  body {
    background: var(--bg);
    font-family: "Lato", Arial, sans-serif;
    position: relative;
  }
  .card {
    position: absolute;
    left: 91px; top: 304px;
    width: 1015px; height: 592px;
    background: var(--card);
    border-radius: 48px 48px 48px 12px;
    overflow: hidden;
  }
  .accent-tab {
    position: absolute; left: 0; top: 131px;
    width: 13px; height: 72px; background: var(--red);
  }
  .identity { position: absolute; left: 65px; top: 124px; }
  .person-name {
    color: var(--red); font-weight: 700; font-size: 34px; line-height: 1.2;
  }
  .person-role {
    color: var(--ink); font-size: 22px; margin-top: 6px;
  }
  .contact-list {
    position: absolute; left: 65px; top: 252px;
    list-style: none;
  }
  .contact-list li {
    display: flex; align-items: center; gap: 10px;
    height: 31.5px; font-size: 19px; color: var(--text);
  }
  .contact-list svg { width: 15px; height: 15px; fill: var(--red); flex: none; }
  .brand {
    position: absolute; right: 50px; top: 118px;
    display: flex; align-items: center; gap: 16px;
  }
  .brand-dot { width: 70px; height: 70px; border-radius: 50%; background: var(--red); }
  .brand-name {
    font-weight: 900; font-size: 40px; color: var(--charcoal);
    text-transform: uppercase; letter-spacing: 1px;
  }
  .office {
    position: absolute; top: 408px;
    color: var(--text); font-size: 15.5px; line-height: 23.5px;
  }
  .office h3 {
    color: var(--red); font-weight: 400; font-size: 24px;
    line-height: 30px; margin-bottom: 4px;
  }
  .office--head { left: 65px; }
  .office--dubai { left: 408px; top: 404px; }
  .office--qatar { left: 755px; top: 404px; }
  .divider {
    position: absolute; top: 413px; width: 2px; height: 123px; background: var(--red);
  }
  .divider--one { left: 360px; }
  .divider--two { left: 684px; }
  .base-band {
    position: absolute; left: 0; right: 0; bottom: 0; height: 29px;
    display: flex;
  }
  .base-band .dark { width: 65px; background: var(--charcoal); }
  .base-band .red { flex: 1; background: var(--red); }
</style>
</head>
<body>
  <div class="card">
    <div class="accent-tab"></div>

    <div class="identity">
      <h1 class="person-name">Sami Darwell</h1>
      <p class="person-role">Managing Partner</p>
    </div>

    <ul class="contact-list">
      <li>
        <svg viewBox="0 0 24 24" aria-hidden="true"><path d="M6.6 10.8a15.1 15.1 0 0 0 6.6 6.6l2.2-2.2a1 1 0 0 1 1-.25 11.4 11.4 0 0 0 3.6.57 1 1 0 0 1 1 1V20a1 1 0 0 1-1 1A17 17 0 0 1 3 4a1 1 0 0 1 1-1h3.5a1 1 0 0 1 1 1c0 1.25.2 2.45.57 3.6a1 1 0 0 1-.25 1z"/></svg>
        +971 (0)50 555 0147
      </li>
      <li>
        <svg viewBox="0 0 24 24" aria-hidden="true"><path d="M2 5h20v2l-10 6L2 7z"/><path d="M2 9l10 6 10-6v10H2z"/></svg>
        sami@tormingroup.com
      </li>
      <li>
        <svg viewBox="0 0 24 24" aria-hidden="true"><path d="M12 2a10 10 0 1 0 0 20 10 10 0 0 0 0-20zm-1 17.9A8 8 0 0 1 4.1 11H7c.1 2.6.7 5 1.7 6.7.6.9 1.4 1.7 2.3 2.2zM9 11h6c-.2 3.4-1.5 6.3-3 7.6-1.5-1.3-2.8-4.2-3-7.6zm0-2c.2-3.4 1.5-6.3 3-7.6 1.5 1.3 2.8 4.2 3 7.6zm8 2h2.9a8 8 0 0 1-6.9 8.9c.9-.5 1.7-1.3 2.3-2.2 1-1.7 1.6-4.1 1.7-6.7zm0-2c-.1-2.6-.7-5-1.7-6.7A8 8 0 0 1 19.9 9zM7 9H4.1A8 8 0 0 1 11 4.1C10.1 4.6 9.3 5.4 8.7 6.3 7.7 8 7.1 6.4 7 9z"/></svg>
        www.tormingroup.com
      </li>
    </ul>

    <div class="brand">
      <span class="brand-dot"></span>
      <span class="brand-name">Tormin Group</span>
    </div>

    <section class="office office--head">
      <h3>Head Office</h3>
      <p>P.O. Box: 10482 Abu Dhabi. U.A.E</p>
      <p>Tel No: +971 (0)2 5550184</p>
      <p>Fax No: +971(0)2 5550185</p>
      <p>Email: sales@tormingroup.com</p>
    </section>
    <div class="divider divider--one"></div>

    <section class="office office--dubai">
      <h3>Dubai Office</h3>
      <p>P.O. Box: 207315 Dubai, U.A.E</p>
      <p>Tel No: +971 (0)4 555026</p>
      <p>Fax No: +971(0)4 555027</p>
      <p>Email: sales@tormingroup.com</p>
    </section>
    <div class="divider divider--two"></div>

    <section class="office office--qatar">
      <h3>Qater Office</h3>
      <p>P.O. Box: 30928 Doha, Qatter</p>
      <p>Tel No: +974 55501936</p>
      <p>Fax No: +971 55507712</p>
      <p>Email: sales@tormingroup.com</p>
    </section>

    <div class="base-band"><span class="dark"></span><span class="red"></span></div>
  </div>
</body>
</html>
```